Media Services Start-up -- Corporate Website and Logo Design. Inspiration required!

We need a logo design and corporate website design, including coding, for our start-up business.
Vennatra’s value proposition is based on bringing together media content from a vast number of geographies globally, adding human and AI curation, translation and editing, and delivering the content using tailored customer interfaces. On the one hand, the business brings together media coverage from all over the world, and on the other it brings together content, human skills and technology to deliver a supreme customer experience.
Vennatra is a B2B media monitoring and analytics business with emphasis on global customers. Vennatra's service offering is centred around sourcing media content from different markets, processing, storing and delivering the content and insights derived from it using an online platform / mobile app.
The messaging we want to create through the logo is:
- Global scope
- Speed of delivery
- Cost-efficiency
- Multi-lingual
- Tailor-made
- Trustworthy
Target Market(s)
Business to business, PR / Communications, Media, Marketing
Logo Text
Vennatra
Coding
Coded - Design and coding required
Number of Pages Required
5+ page
Font styles to use
Other font styles liked:
- See Design Brief for details
Colors
Designer to choose colors to be used in the design.

```html
<!DOCTYPE html>
<html lang="en">
<head>
<meta charset="utf-8">
<title>Vennatra — Global Media Intelligence</title>
<link href="https://fonts.googleapis.com/css2?family=Mulish:wght@400;600;700;800&display=swap" rel="stylesheet">
<style>
  :root {
    --ink: #3a3a3a;
    --white: #ffffff;
    --panel: rgba(255,255,255,0.82);
    --panel-inner: #f7f7f7;
    --field-border: #d9d9d9;
    --icon: #555555;
    --accent: #2aa198;
    --req: #e23b3b;
    --footer: #121820;
    --hero-deep: #0b1a33;
    --hero-blue: #1c3f7a;
    --hero-green: #2f6b3a;
  }
  * { box-sizing: border-box; margin: 0; padding: 0; }
  html, body { width: 1200px; height: 544px; overflow: hidden; }
  body { font-family: 'Mulish', sans-serif; background: var(--white); position: relative; }

  .site-header { position: absolute; left: 0; top: 0; width: 1200px; height: 56px; background: var(--white); }
  .brand { position: absolute; left: 144px; top: 2px; font-size: 41px; font-weight: 700; color: var(--ink); letter-spacing: 0.5px; }
  .contact { position: absolute; top: 18px; display: flex; align-items: center; gap: 7px; font-size: 15px; color: var(--ink); }
  .contact.phone { left: 696px; }
  .contact.email { left: 847px; }
  .menu-toggle { position: absolute; left: 1022px; top: 12px; width: 37px; height: 33px; border: 2px solid var(--accent); display: flex; flex-direction: column; justify-content: center; align-items: flex-end; gap: 6px; padding-right: 5px; }
  .menu-toggle span { display: block; height: 2px; background: var(--accent); }

  .hero { position: absolute; left: 0; top: 56px; width: 1200px; height: 452px; overflow: hidden; }
  .hero-visual { position: absolute; inset: 0;
    background:
      radial-gradient(ellipse at 40% 30%, rgba(70,110,220,0.75), transparent 55%),
      radial-gradient(ellipse at 95% 70%, rgba(70,150,80,0.7), transparent 55%),
      linear-gradient(180deg, var(--hero-deep) 0%, var(--hero-blue) 55%, #15233a 100%); }
  .hero-visual::after { content: ""; position: absolute; inset: 0; background: linear-gradient(180deg, rgba(0,0,0,0) 60%, rgba(0,0,0,0.35) 100%); }

  .hero-copy { position: absolute; left: 143px; top: 262px; width: 560px; color: var(--white); }
  .hero-copy h1 { font-size: 27px; font-weight: 800; letter-spacing: 0.2px; line-height: 1.1; }
  .hero-copy p { margin-top: 12px; font-size: 18px; font-weight: 700; line-height: 26.5px; }

  .lead-form { position: absolute; left: 748px; top: 66px; width: 312px; height: 339px; background: var(--panel); padding: 10px 11px; }
  .lead-form .inner { width: 100%; height: 100%; background: var(--panel-inner); padding: 28px 13px 0; }
  .lead-form h2 { text-align: center; font-size: 21px; font-weight: 700; color: #1d1d1d; line-height: 26px; margin-bottom: 18px; }
  .field { display: flex; height: 42px; border: 1px solid var(--field-border); background: var(--white); margin-bottom: 15px; }
  .field .ico { width: 36px; border-right: 1px solid var(--field-border); display: flex; align-items: center; justify-content: center; }
  .field .label { padding-left: 11px; display: flex; align-items: center; font-size: 13px; color: #555; }
  .field .label em { color: var(--req); font-style: normal; margin-left: 4px; }
  .btn-start { display: flex; align-items: center; justify-content: center; height: 43px; border: 2px solid var(--accent); background: var(--white); font-size: 18px; font-weight: 600; color: #1d1d1d; letter-spacing: 0.3px; margin-top: 7px; }

  .site-footer { position: absolute; left: 0; top: 508px; width: 1200px; height: 36px; background: var(--footer); color: var(--white); font-size: 13px; }
  .site-footer .copy { position: absolute; left: 142px; top: 10px; }
  .social { position: absolute; left: 918px; top: 9px; display: flex; align-items: center; gap: 10px; }
  .social .dot { width: 14px; height: 14px; border-radius: 50%; background: var(--white); }
</style>
</head>
<body>
  <header class="site-header">
    <div class="brand">Vennatra</div>
    <div class="contact phone">
      <svg width="15" height="15" viewBox="0 0 24 24"><path fill="#1d1d1d" d="M6.6 10.8a15.1 15.1 0 0 0 6.6 6.6l2.2-2.2c.3-.3.7-.4 1-.2 1.1.4 2.3.6 3.6.6.6 0 1 .4 1 1V20c0 .6-.4 1-1 1A17 17 0 0 1 3 4c0-.6.4-1 1-1h3.5c.6 0 1 .4 1 1 0 1.3.2 2.5.6 3.6.1.3 0 .7-.2 1z"/></svg>
      <span>+1 555 010 2040</span>
    </div>
    <div class="contact email">
      <svg width="20" height="15" viewBox="0 0 20 15"><rect x="0.5" y="0.5" width="19" height="14" fill="#1d1d1d"/><path d="M1 1l9 7 9-7M1 14l6.5-6M19 14l-6.5-6" stroke="#fff" stroke-width="1.2" fill="none"/></svg>
      <span>info@vennatra.com</span>
    </div>
    <div class="menu-toggle" aria-label="Menu">
      <span style="width:24px"></span><span style="width:24px"></span><span style="width:24px"></span>
    </div>
  </header>

  <section class="hero">
    <div class="hero-visual" role="img" aria-label="Businessman holding a phone before a wall of global news screens, world maps and charts"></div>
    <div class="hero-copy">
      <h1>DELIVERING GLOBAL MEDIA INTELLIGENCE</h1>
      <p>Vennatra is an international media intelligence service provider. We help communications teams build and operate truly global media monitoring and measurement programmes.</p>
    </div>

    <form class="lead-form">
      <div class="inner">
        <h2>Learn More<br>About Vennatra</h2>
        <div class="field">
          <div class="ico"><svg width="14" height="14" viewBox="0 0 14 14"><circle cx="7" cy="4" r="3.2" fill="var(--icon)"/><path d="M1 14c0-3.5 2.7-5.5 6-5.5s6 2 6 5.5z" fill="var(--icon)"/></svg></div>
          <div class="label">Your Name<em>*</em></div>
        </div>
        <div class="field">
          <div class="ico"><svg width="14" height="11" viewBox="0 0 20 15"><rect x="0.5" y="0.5" width="19" height="14" fill="var(--icon)"/><path d="M1 1l9 7 9-7M1 14l6.5-6M19 14l-6.5-6" stroke="#fff" stroke-width="1.4" fill="none"/></svg></div>
          <div class="label">Your Email<em>*</em></div>
        </div>
        <div class="field">
          <div class="ico"><svg width="13" height="13" viewBox="0 0 24 24"><path fill="var(--icon)" d="M6.6 10.8a15.1 15.1 0 0 0 6.6 6.6l2.2-2.2c.3-.3.7-.4 1-.2 1.1.4 2.3.6 3.6.6.6 0 1 .4 1 1V20c0 .6-.4 1-1 1A17 17 0 0 1 3 4c0-.6.4-1 1-1h3.5c.6 0 1 .4 1 1 0 1.3.2 2.5.6 3.6.1.3 0 .7-.2 1z"/></svg></div>
          <div class="label">Your Phone<em>*</em></div>
        </div>
        <div class="btn-start">GET STARTED</div>
      </div>
    </form>
  </section>

  <footer class="site-footer">
    <div class="copy">Copyright © 2019 Vennatra. All Rights Reserved.</div>
    <div class="social">
      <span>Follow Us :</span>
      <span class="dot" aria-label="Social link"></span>
      <span class="dot" aria-label="Social link"></span>
      <span class="dot" aria-label="Social link"></span>
    </div>
  </footer>
</body>
</html>
```